A start up special flyer design!

Hi All - Have updated the attachment content - This is the info required for the designs.
I need a catchy flyer to send out to a few areas to advertise the start of my plumbing business!
The flyer will contain an offer for customers, which will need to have some key details on it. See attached. Feel free to fit these criteria into the flyer given your knowledge on design and messaging principles. Key thing to get across to customers is the discount and special offer, and that it is a start up offer.
I have a logo that needs to be on the flyer as well - let me know what format you require and I will send through to you.
The color scheme needs to be blue / grey / black / white.
Let me know if you have any questions.
I

```html
<!DOCTYPE html>
<html lang="en">
<head>
<meta charset="utf-8">
<title>Brookflow Plumbing – Start-up Offer Flyer</title>
<link href="https://fonts.googleapis.com/css2?family=Roboto+Condensed:wght@400;700&display=swap" rel="stylesheet">
<style>
  :root{
    --blue:#1aa3ee;
    --blue-deep:#0f8fe0;
    --cyan:#22c8ee;
    --charcoal:#262626;
    --ink:#222;
    --white:#fff;
    --mist:#eef1f4;
    --page:#ececec;
  }
  *{margin:0;padding:0;box-sizing:border-box}
  html,body{width:825px;height:1200px;overflow:hidden;background:var(--page)}
  body{position:relative;font-family:"Roboto Condensed",sans-serif;color:var(--ink)}
  .flyer{position:absolute;left:107px;top:167px;width:613px;height:866px;overflow:hidden;
    background:linear-gradient(180deg,#f4f6f8 0%,#e9eef2 55%,#f7f8f9 100%)}
  .flyer > *{position:absolute}
  .art{left:0;top:0;width:613px;height:866px}
  .tagline{left:0;top:28px;width:316px;text-align:center;font-weight:700;font-size:29px;line-height:32px;letter-spacing:-.3px}
  .tagline .lead{color:var(--white)}
  .tagline .rest{color:var(--charcoal)}
  .brand{left:0;top:128px;width:316px;text-align:center;font-weight:700;line-height:1}
  .brand .name{display:block;font-size:37px;color:var(--charcoal);letter-spacing:.3px}
  .brand .trade{display:block;font-size:55px;color:var(--blue);margin-top:4px;letter-spacing:.5px}
  .offer{left:28px;top:288px;width:283px;text-align:center;font-weight:700;line-height:1}
  .offer .amount{display:block;font-size:64px;color:var(--cyan)}
  .offer .subject{display:block;font-size:29px;color:var(--white);margin-top:6px;letter-spacing:-.2px}
  .terms{right:30px;top:377px;list-style:none;text-align:right;font-weight:700;font-size:15px;line-height:22px;color:var(--charcoal)}
  .terms li{position:relative;padding-right:28px}
  .terms li::after{content:"";position:absolute;right:0;top:6px;width:11px;height:11px;border-radius:50%;background:var(--blue)}
  .terms li.cont::after{display:none}
  .bonus{left:48px;top:477px;width:526px;height:38px;border-radius:0 19px 19px 0;
    background:linear-gradient(90deg,var(--blue-deep),var(--blue));border-left:3px solid var(--charcoal);
    color:var(--white);font-weight:700;font-size:19.5px;line-height:38px;text-align:center}
  .contact{left:0;top:728px;width:613px;text-align:center;color:var(--white);font-weight:700;font-size:20px;line-height:30px}
  .contact .label{color:var(--cyan)}
  .usp{left:68px;top:805px;width:470px;height:35px;border-radius:0 18px 18px 0;background:var(--cyan);
    display:flex;align-items:center;font-weight:700;font-size:17px;color:var(--charcoal)}
  .usp .item{display:flex;align-items:center;gap:10px}
  .usp .item:first-child{margin-left:20px;margin-right:20px}
  .usp svg{display:block}
</style>
</head>
<body>
<main class="flyer">
  <svg class="art" viewBox="0 0 613 866" xmlns="http://www.w3.org/2000/svg">
    <defs>
      <linearGradient id="bandGrad" x1="0" y1="0" x2="0" y2="1">
        <stop offset="0" stop-color="#ffffff"/>
        <stop offset="1" stop-color="#dfe4e8"/>
      </linearGradient>
      <linearGradient id="heroGrad" x1="0" y1="0" x2="1" y2="1">
        <stop offset="0" stop-color="#eef0f2"/>
        <stop offset=".5" stop-color="#d9c2b3"/>
        <stop offset="1" stop-color="#c9ccd0"/>
      </linearGradient>
      <radialGradient id="jobGrad" cx=".5" cy=".5" r=".6">
        <stop offset="0" stop-color="#d8cfc8"/>
        <stop offset="1" stop-color="#aab4bd"/>
      </radialGradient>
    </defs>
    <!-- top blue block and band -->
    <rect class="top-block" x="0" y="0" width="330" height="118" fill="#1aa3ee"/>
    <rect class="name-band" x="0" y="116" width="320" height="117" fill="url(#bandGrad)"/>
    <rect class="under-band" x="0" y="233" width="330" height="32" fill="#1aa3ee"/>
    <!-- hero photo area -->
    <polygon points="298,0 613,0 613,338 348,288" fill="#262626"/>
    <polygon role="img" aria-label="Photo: plumber's hands tightening a pipe fitting under a basin with a wrench" points="312,0 613,0 613,330 356,280" fill="url(#heroGrad)"/>
    <polygon points="322,290 613,342 613,356 335,300" fill="#22c8ee"/>
    <!-- offer badge -->
    <polygon points="38,276 322,276 322,418 180,440 38,418" fill="#22c8ee"/>
    <polygon points="28,265 311,265 311,408 170,432 28,408" fill="#262626"/>
    <!-- job photos -->
    <g class="job-photos">
      <circle cx="111" cy="613" r="73" fill="#1aa3ee"/>
      <circle cx="111" cy="613" r="64" fill="#22c8ee"/>
      <circle role="img" aria-label="Photo: plumbers inspecting pipes under a kitchen sink" cx="111" cy="613" r="58" fill="url(#jobGrad)"/>
      <circle cx="303" cy="613" r="73" fill="#1aa3ee"/>
      <circle cx="303" cy="613" r="64" fill="#22c8ee"/>
      <circle role="img" aria-label="Photo: hands fitting copper pipe with a wrench" cx="303" cy="613" r="58" fill="url(#jobGrad)"/>
      <circle cx="478" cy="613" r="73" fill="#1aa3ee"/>
      <circle cx="478" cy="613" r="64" fill="#22c8ee"/>
      <circle role="img" aria-label="Photo: chrome wall tap being installed on tiles" cx="478" cy="613" r="58" fill="url(#jobGrad)"/>
    </g>
    <!-- footer -->
    <rect x="0" y="691" width="613" height="9" fill="#1aa3ee"/>
    <rect x="0" y="699" width="613" height="167" fill="#262626"/>
  </svg>

  <h2 class="tagline"><span class="lead">All plumbing, draining</span><br><span class="rest">and gasfitting works</span></h2>
  <h1 class="brand"><span class="name">BROOKFLOW</span><span class="trade">PLUMBING</span></h1>

  <div class="offer"><span class="amount">15% OFF</span><span class="subject">YOUR OVERALL BILL</span></div>

  <ul class="terms">
    <li>Offer expires 30 September 2016</li>
    <li>Quote valid for 12 months from</li>
    <li class="cont">the quote date</li>
  </ul>

  <p class="bonus">Plus, a free hot water health check and replacement quote</p>

  <address class="contact" style="font-style:normal">
    <span class="label">Ph:</span> 0491 570 118 <span class="label">| Email:</span> sam@brookflowplumbing.co<br>
    <span class="label">Web:</span> www.brookflowplumbing.com
  </address>

  <div class="usp">
    <span class="item">
      <svg width="20" height="26" viewBox="0 0 20 26" aria-hidden="true"><path d="M10 1a8 8 0 0 1 8 8c0 6-8 15-8 15S2 15 2 9a8 8 0 0 1 8-8z" fill="#fff"/><circle cx="10" cy="9" r="3.2" fill="#22c8ee"/><ellipse cx="10" cy="24.5" rx="6" ry="1.3" fill="#fff"/></svg>
      Local plumber
    </span>
    <span class="item">
      <svg width="24" height="22" viewBox="0 0 24 22" aria-hidden="true"><rect x="1" y="9" width="5" height="12" fill="#fff"/><path d="M8 9l5-8c2 0 3 1 2.5 3L14 8h7c1.5 0 2.5 1.5 2 3l-2.5 8c-.4 1.3-1.4 2-2.6 2H8z" fill="#fff"/></svg>
      Quality work at a decent price
    </span>
  </div>
</main>
</body>
</html>
```